KVOR Individual and Corporate Development Business Card Design

KVOR needs a business card design that is aligned with it's values and targetted markets. Coherent Lattice of Adaptive Reasoning Method's self diagnosis model and tools, which can be used for personal improvement and team/business performance enhancement, is based on the learnings of over 20 years of medical practitioning. KVOR supercharges personal effectiveness and awareness to also increase team and business performance.

The targetted markets are high performance individuals and teams who aspire seek to enhance their capabilities and achieve their absolute best potential.

Look and feel for the business card design we are looking for is high technology, premium, fresh, new and medical.

Target Market(s)

Industry/Entity Type

Business Consultant

Contact Information for Business Card

Logo, Full Name, Title, Phone number, Email, company name, Address,

Font styles to use
Sans Serif

Requirements
Must have
• Tag line: Elevating Output for Consistently Focused Teams
• Please use same colours as the logo.

```html
<!DOCTYPE html>
<html lang="en">
<head>
<meta charset="utf-8">
<title>KVOR Business Card</title>
<link rel="stylesheet" href="https://fonts.googleapis.com/css2?family=Open+Sans:wght@400;600;700&display=swap">
<style>
  :root {
    --stage: #2b2826;
    --card-black: #0d0d0e;
    --brand-cyan: #00a8c2;
    --band-dark: #262729;
    --text-light: #e9eef0;
    --rule-grey: #5d6468;
  }
  * { box-sizing: border-box; margin: 0; padding: 0; }
  html, body {
    width: 1200px; height: 900px; overflow: hidden;
    background: var(--stage);
    font-family: "Open Sans", sans-serif;
  }
  .stage { position: relative; width: 1200px; height: 900px; }
  .card {
    position: absolute; width: 510px; height: 292px; top: 304px;
    border-radius: 3px;
    box-shadow: 0 10px 30px rgba(0,0,0,.45);
    overflow: hidden;
  }
  .card-front { left: 60px; background: var(--card-black); }
  .card-back { left: 630px; background: var(--brand-cyan); }

  .wordmark {
    position: absolute; left: 0; right: 0; text-align: center;
    display: flex; flex-direction: column; align-items: center;
  }
  .wordmark-name {
    font-weight: 700; font-size: 66px; line-height: 1; letter-spacing: 4px;
    color: var(--brand-cyan);
  }
  .wordmark-rule {
    width: 280px; height: 1px; background: var(--rule-grey); margin: 6px 0 5px;
  }
  .wordmark-full {
    font-weight: 600; font-size: 13px; line-height: 1.2; letter-spacing: .6px;
    text-transform: uppercase; color: var(--brand-cyan); width: 280px;
  }
  .card-front .wordmark { top: 30px; }
  .card-back .wordmark { top: 40px; }
  .card-back .wordmark-name,
  .card-back .wordmark-full { color: #ffffff; }
  .card-back .wordmark-rule { background: rgba(255,255,255,.55); }

  .person { position: absolute; left: 34px; top: 180px; color: var(--text-light); }
  .person-name {
    font-weight: 600; font-size: 17px; letter-spacing: .5px;
    text-transform: uppercase; color: var(--brand-cyan);
  }
  .person-title { font-size: 14px; margin-top: 1px; }
  .person-address { font-size: 14px; line-height: 1.3; margin-top: 16px; }

  .contacts {
    position: absolute; right: 30px; top: 152px;
    list-style: none; color: var(--text-light); font-size: 13px;
  }
  .contacts li {
    display: flex; align-items: center; justify-content: flex-end;
    gap: 6px; height: 21px;
  }
  .contacts svg { width: 13px; height: 13px; }

  .tagline-band {
    position: absolute; left: 0; right: 0; bottom: 0; height: 82px;
    background: var(--band-dark);
    display: flex; align-items: center; padding-left: 24px;
    border-top: 2px solid rgba(255,255,255,.15);
  }
  .tagline {
    font-weight: 600; font-size: 12.5px; letter-spacing: 1.4px;
    text-transform: uppercase; color: var(--brand-cyan);
  }
</style>
</head>
<body>
<main class="stage">

  <section class="card card-front" aria-label="Business card front">
    <div class="wordmark">
      <span class="wordmark-name">KVOR</span>
      <span class="wordmark-rule"></span>
      <span class="wordmark-full">Coherent Lattice of Adaptive Reasoning Method</span>
    </div>

    <div class="person">
      <p class="person-name">Marcus Eldridge</p>
      <p class="person-title">Managing Director</p>
      <p class="person-address">Address line one here,<br>Address line two here.</p>
    </div>

    <ul class="contacts">
      <li>888 555 742
        <svg viewBox="0 0 14 14" aria-hidden="true"><circle cx="7" cy="7" r="7" fill="#fff"/><path d="M5 3.5h4v7H5z" fill="none" stroke="#00a8c2" stroke-width="1.2"/></svg>
      </li>
      <li>info@kvor.com
        <svg viewBox="0 0 14 14" aria-hidden="true"><circle cx="7" cy="7" r="7" fill="#fff"/><rect x="3.5" y="4.5" width="7" height="5" fill="#00a8c2"/><path d="M3.5 4.5L7 7.3l3.5-2.8" fill="none" stroke="#fff" stroke-width=".8"/></svg>
      </li>
      <li>www.kvor.com
        <svg viewBox="0 0 14 14" aria-hidden="true"><circle cx="7" cy="7" r="7" fill="#fff"/><circle cx="7" cy="7" r="3.6" fill="none" stroke="#00a8c2" stroke-width="1"/><path d="M3.4 7h7.2M7 3.4v7.2" stroke="#00a8c2" stroke-width=".8"/></svg>
      </li>
    </ul>
  </section>

  <section class="card card-back" aria-label="Business card back">
    <div class="wordmark">
      <span class="wordmark-name">KVOR</span>
      <span class="wordmark-rule"></span>
      <span class="wordmark-full">Coherent Lattice of Adaptive Reasoning Method</span>
    </div>
    <div class="tagline-band">
      <p class="tagline">Elevating Output for Consistently Focused Teams</p>
    </div>
  </section>

</main>
</body>
</html>
```